Spiritual Healing bussiness needs logo/business card

Simple, clean looking logo/card
For spiritual business with healing services and occult rituals

Contact Information for Business Card

Needs my name: Tobin Varley
Business name: Lantern Healing Shop
Services provided and worded in this way:

Reiki Healing
Tarot
Oils
Rituals Of Change

Can look occult like but with light energy.

Colors
0255a3
3276b5
85abd2
33a6d7
85cae6
0292cd

```html
<!DOCTYPE html>
<html lang="en">
<head>
<meta charset="utf-8">
<title>Lantern Healing Shop – Business Card</title>
<link rel="stylesheet" href="https://fonts.googleapis.com/css2?family=Open+Sans:wdth,wght@75,400;75,600&display=swap">
<style>
  :root {
    --navy: #0255a3;
    --mid-blue: #3276b5;
    --soft-blue: #85abd2;
    --sky: #33a6d7;
    --pale-sky: #85cae6;
    --ocean: #0292cd;
  }
  html, body {
    margin: 0;
    padding: 0;
    width: 1200px;
    height: 686px;
    overflow: hidden;
  }
  .card {
    position: relative;
    width: 1200px;
    height: 686px;
    overflow: hidden;
    font-family: "Open Sans", "Myriad Pro", sans-serif;
    font-stretch: 75%;
  }
  .card-waves {
    position: absolute;
    inset: 0;
    width: 100%;
    height: 100%;
  }
  .brand-mark {
    position: absolute;
    top: 172px;
    left: 0;
    width: 100%;
    display: flex;
    justify-content: center;
    align-items: center;
    gap: 12px;
  }
  .brand-mark-square {
    width: 52px;
    height: 52px;
    background: var(--mid-blue);
    opacity: 0.9;
  }
  .brand-mark-name {
    font-size: 26px;
    font-weight: 600;
    color: var(--mid-blue);
  }
  .business-name {
    position: absolute;
    top: 262px;
    left: 0;
    width: 100%;
    margin: 0;
    text-align: center;
    font-size: 118px;
    font-weight: 400;
    letter-spacing: -1px;
    line-height: 1;
    color: var(--navy);
  }
  .services {
    position: absolute;
    top: 430px;
    left: 0;
    width: 100%;
    margin: 0;
    text-align: center;
    font-size: 48px;
    font-weight: 400;
    line-height: 1;
    color: var(--mid-blue);
    opacity: 0.85;
  }
</style>
</head>
<body>
<main class="card">
  <svg class="card-waves" viewBox="0 0 1200 686" preserveAspectRatio="none" aria-hidden="true">
    <defs>
      <linearGradient id="sky-fade" x1="0" y1="0" x2="1" y2="1">
        <stop offset="0" stop-color="#f2faff"/>
        <stop offset="0.35" stop-color="#9fd3f0"/>
        <stop offset="0.65" stop-color="#3f95df"/>
        <stop offset="1" stop-color="#1a5fce"/>
      </linearGradient>
    </defs>
    <rect width="1200" height="686" fill="url(#sky-fade)"/>
    <path d="M0 170 C 300 150, 700 200, 1200 330 L1200 686 L0 686 Z" fill="#ffffff" opacity="0.12"/>
    <path d="M0 330 C 350 330, 800 420, 1200 560 L1200 686 L0 686 Z" fill="#1e6fd6" opacity="0.25"/>
    <path d="M0 470 C 300 440, 700 500, 1100 686 L0 686 Z" fill="#ffffff" opacity="0.1"/>
    <path d="M0 560 C 250 520, 550 560, 760 686 L0 686 Z" fill="#1450c4" opacity="0.3"/>
    <path d="M420 0 C 560 180, 760 330, 1200 420 L1200 0 Z" fill="#ffffff" opacity="0.1"/>
    <path d="M760 0 C 860 140, 1020 220, 1200 250 L1200 0 Z" fill="#2a86e0" opacity="0.35"/>
    <path d="M300 686 C 500 520, 800 420, 1200 380 L1200 686 Z" fill="#0f4fc0" opacity="0.22"/>
    <path d="M1080 686 C 1120 620, 1160 590, 1200 580 L1200 686 Z" fill="#5fb3ea" opacity="0.5"/>
  </svg>

  <div class="brand-mark">
    <span class="brand-mark-square"></span>
    <span class="brand-mark-name">Lantern Healing Shop</span>
  </div>

  <h1 class="business-name">Lantern Healing Shop</h1>
  <p class="services">Reiki Healing| Tarot | Oils | Rituals Of Change</p>
</main>
</body>
</html>
```